Northfield Builders Guild Business card

We are looking for a new business card design with photo included.
Our business is a nonprofit construction contractor membership organization. We offer business education, assist with business setup and licensing, provide safety training, and provide a member directory.
URL: www.builderslinkguild.org
Color code:
CMYK: 0 cyan, 42 magenta, 100 yellow, 0 black for Print.
Hexidecimal: #FF9900
RGB: R 255; G 153; B 0

```html
<!DOCTYPE html>
<html lang="en">
<head>
<meta charset="utf-8">
<title>Northfield Builders Guild – Business Card</title>
<link href="https://fonts.googleapis.com/css2?family=Michroma&family=Open+Sans:wght@400;800&display=swap" rel="stylesheet">
<style>
  :root {
    --orange: #f7991f;
    --charcoal: #333132;
    --ink: #3a3a3a;
    --paper: #ffffff;
    --backdrop: #4a4a4a;
  }
  * { margin: 0; padding: 0; box-sizing: border-box; }
  html, body { width: 1200px; height: 751px; overflow: hidden; }
  body { background: var(--backdrop); position: relative; font-family: "Open Sans", sans-serif; }

  .card {
    position: absolute;
    width: 493px; height: 282px;
    background: var(--paper);
    overflow: hidden;
  }
  .card--front { left: 90px; top: 218px; }
  .card--back  { left: 619px; top: 218px; }

  .holder { position: absolute; left: 21px; top: 58px; }
  .holder__name {
    font-family: "Michroma", sans-serif;
    font-size: 12.5px; letter-spacing: 3px;
    color: var(--orange); line-height: 1;
  }
  .holder__title { font-size: 9.5px; color: var(--ink); margin-top: 4px; }

  .contacts { position: absolute; left: 21px; top: 132px; list-style: none; }
  .contacts li {
    display: flex; align-items: center; gap: 7px;
    height: 21px; margin-bottom: 2.5px;
    font-size: 11px; color: var(--ink);
  }
  .contacts svg { width: 21px; height: 21px; flex: none; }

  .wordmark {
    position: absolute;
    display: flex; align-items: center; gap: 8px;
    font-weight: 800; color: var(--charcoal);
    line-height: 1.02; text-transform: uppercase;
  }
  .wordmark__mark { background: var(--orange); flex: none; }
  .card--front .wordmark { left: 276px; top: 112px; font-size: 21px; }
  .card--front .wordmark__mark { width: 14px; height: 14px; }
  .card--back .wordmark { left: 50%; top: 50%; transform: translate(-50%, -50%); font-size: 27px; }
  .card--back .wordmark__mark { width: 18px; height: 18px; }

  .band { position: absolute; left: 0; bottom: 0; width: 493px; height: 28px; }
</style>
</head>
<body>

<section class="card card--front">
  <div class="holder">
    <p class="holder__name">DANIEL REYES</p>
    <p class="holder__title">CEO/Managing Director</p>
  </div>

  <ul class="contacts">
    <li>
      <svg viewBox="0 0 21 21" aria-hidden="true"><circle cx="10.5" cy="10.5" r="9.5" fill="none" stroke="var(--orange)" stroke-width="1.3"/><rect x="7" y="4.5" width="7" height="12" rx="1.2" fill="none" stroke="var(--orange)" stroke-width="1.2"/><circle cx="10.5" cy="14.5" r="0.7" fill="var(--orange)"/></svg>
      <span>214-555-0142</span>
    </li>
    <li>
      <svg viewBox="0 0 21 21" aria-hidden="true"><circle cx="10.5" cy="10.5" r="9.5" fill="none" stroke="var(--orange)" stroke-width="1.3"/><path d="M5 10.5 L10.5 5.5 L16 10.5 H14.5 V15.5 H6.5 V10.5 Z" fill="var(--orange)"/></svg>
      <span>214-555-0142</span>
    </li>
    <li>
      <svg viewBox="0 0 21 21" aria-hidden="true"><circle cx="10.5" cy="10.5" r="9.5" fill="none" stroke="var(--orange)" stroke-width="1.3"/><rect x="5.5" y="7" width="10" height="7" fill="var(--orange)"/><path d="M5.5 7 L10.5 11 L15.5 7" fill="none" stroke="#fff" stroke-width="0.9"/></svg>
      <span>dreyes@builderslinkguild.org</span>
    </li>
    <li>
      <svg viewBox="0 0 21 21" aria-hidden="true"><circle cx="10.5" cy="10.5" r="9.5" fill="none" stroke="var(--orange)" stroke-width="1.3"/><g fill="none" stroke="var(--orange)" stroke-width="0.9"><circle cx="10.5" cy="10.5" r="5.5"/><ellipse cx="10.5" cy="10.5" rx="2.4" ry="5.5"/><path d="M5 10.5 H16 M6 7.8 H15 M6 13.2 H15"/></g></svg>
      <span>&nbsp;www.builderslinkguild.org</span>
    </li>
  </ul>

  <div class="wordmark">
    <span class="wordmark__mark"></span>
    <span>Northfield<br>Builders Guild</span>
  </div>

  <svg class="band" viewBox="0 0 493 28" aria-hidden="true">
    <polygon points="0,0 374,0 387,14 374,28 0,28" fill="var(--orange)"/>
    <polygon points="385,0 493,0 493,28 385,28 398,14" fill="var(--charcoal)"/>
  </svg>
</section>

<section class="card card--back">
  <div class="wordmark">
    <span class="wordmark__mark"></span>
    <span>Northfield<br>Builders Guild</span>
  </div>
</section>

</body>
</html>
```